Website for Reiki and Wellness Courses

I teach online courses in Reiki and wellness/self-development and am needing a new website.

The focus of the website will be to provide descriptions of the courses as well as include a blog and pages where students in my courses will visit for additional information.

Note: courses are NOT hosted on this site.
The focus of this website will be to encourage viewers to enroll in courses as well as opt in to the email list.

I will upload copy soon. My old website is: http://brightfernstudies.example. Please do not use existing logo.

Target Market(s)

Alternative health, wellness, spirituality, personal development. Males and females of all ages seeking to improve their health and life.

Industry/Entity Type

Health And Wellness

Logo Text

No text (please do not use existing logo)

Coding

Coded - Design and coding required

Number of Pages Required

5+ page

Requirements
Must have
• 1. Home page
• 2. About page
• 3. Courses page that outlines courses (there are currently 6 courses with 1 coming soon)
• 4. Individual course page (maybe a template that I can adjust color and pictures for with each course)
• 5. Blog
• 6. Student Area that outlines all Student Areas
• 7. Individual Student Area page (maybe a template that I can adjust color and pictures for with each course)
• 8. Shop page (note: items will not currently be purchased through website - it will be a link to quillmarket for a book).
• 9. Student thank-you page (maybe a template that I can adjust color and pictures for with each course) this is the page students are directed to at end of course with vouchers for other courses.
• Opt-in for the home page, course pages, blog and thank-you pages
Nice to have
• I would like the design to be calm, clean and soothing. Ideally visitors feel relaxed when viewing the site and are encouraged to explore the courses, subscribe to the email list and purchase a product.
• ~ Testimonials page
• ~ Contact page
• I tend to gravitate towards blues, greys and purples as well as monochromatic color schemes.
Should not have
• Contact form on home page
• phone number on home page
• location/physical address
• dates for blog posts

```html
<!DOCTYPE html>
<html lang="en">
<head>
<meta charset="utf-8">
<title>Bright Fern Studies — Reiki and Wellness Self-Development</title>
<link rel="stylesheet" href="https://fonts.googleapis.com/css2?family=Oswald:wght@500;600&family=Roboto:wght@400;500;700&family=Open+Sans:ital,wght@0,400;0,600;1,400&display=swap">
<style>
:root{
  --slate:#6b6e8c;
  --slate-dark:#5d607e;
  --slate-deep:#4f5270;
  --ink:#333;
  --text:#666;
  --muted:#888;
  --line:#ddd;
  --paper:#fff;
  --soft:#f7f7f7;
  --red:#e0334a;
  --nav-active:#2b2b2b;
}
*{margin:0;padding:0;box-sizing:border-box}
html,body{width:1200px;height:2284px;overflow:hidden;background:var(--paper)}
body{font-family:"Open Sans",sans-serif;color:var(--text);position:relative}
.page{position:relative;width:1200px;height:2284px}
.abs{position:absolute}

/* header */
.header{position:absolute;top:0;left:0;width:1200px;height:131px;background:var(--paper)}
.brand{left:99px;top:38px;display:flex;align-items:center;gap:12px}
.brand-mark{width:40px;height:40px;background:var(--slate)}
.brand-name{font-family:"Roboto",sans-serif;font-size:25px;font-weight:400;color:var(--slate)}
.search{left:860px;top:21px;width:241px;height:36px;border:1px solid var(--line);font-size:12px;color:var(--muted);padding:10px 12px}
.search svg{position:absolute;right:12px;top:12px}
.nav{left:460px;top:79px;width:641px;height:52px;background:var(--slate);display:flex;clip-path:polygon(12px 0,100% 0,100% 100%,0 100%)}
.nav a{font-family:"Roboto",sans-serif;font-size:12.5px;color:#fff;text-decoration:none;display:flex;align-items:center;justify-content:center;height:52px;padding:0 26px}
.nav a.active{background:var(--nav-active);padding:0 30px 0 36px}

/* hero */
.hero{left:0;top:131px;width:1200px;height:541px;background:linear-gradient(160deg,#6f7268 0%,#9a9d98 30%,#c9ccc9 55%,#8e938b 80%,#5f665c 100%)}
.hero-kicker{left:0;top:316px;width:1200px;text-align:center;font-family:"Roboto",sans-serif;font-size:27px;color:#fff;letter-spacing:.5px}
.hero-title{left:0;top:362px;width:1200px;text-align:center;font-family:"Oswald",sans-serif;font-weight:600;font-size:50px;color:#fff;letter-spacing:.5px;text-shadow:0 2px 6px rgba(0,0,0,.25)}
.hero-arrow{top:356px}

/* features */
.features{left:0;top:672px;width:1200px;height:233px;background:var(--slate)}
.feature{top:672px;width:334px;height:233px;text-align:center;color:#fff}
.feature.alt{background:var(--slate-dark)}
.feature h3{position:absolute;top:113px;left:0;width:100%;font-family:"Roboto",sans-serif;font-size:15px;font-weight:500;line-height:22px}
.feature p{position:absolute;left:24px;right:24px;font-size:11.5px;line-height:21px}
.diamond{width:134px;height:134px;transform:rotate(45deg);border:4px solid #fff;box-shadow:0 3px 8px rgba(0,0,0,.25)}

/* welcome */
.welcome{left:0;top:905px;width:1200px;height:455px;background:var(--soft);border-bottom:1px solid #eee}
.welcome h2{position:absolute;left:99px;top:60px;font-family:"Roboto",sans-serif;font-size:27px;font-weight:400;color:var(--ink)}
.welcome .copy{position:absolute;left:99px;top:110px;width:650px;font-size:11px;line-height:23px}
.welcome .copy p{margin-bottom:14px}
.btn-more{position:absolute;left:99px;top:335px;width:166px;height:41px;border:2px solid var(--slate);border-radius:3px;display:flex;font-family:"Roboto",sans-serif;font-size:14px;color:var(--slate-dark);background:#fff;overflow:hidden}
.btn-more span{flex:1;display:flex;align-items:center;padding-left:14px}
.btn-more i{width:38px;background:var(--slate);display:flex;align-items:center;justify-content:center}
.optin{position:absolute;left:809px;top:62px;width:292px;height:326px;background:#fff;border:1px solid var(--line);box-shadow:0 10px 14px -6px rgba(0,0,0,.18);text-align:center}
.optin h3{margin-top:22px;font-family:"Roboto",sans-serif;font-size:19px;font-weight:500;color:var(--ink)}
.optin p{margin:8px 30px 0;font-size:11px;line-height:20px}
.field{display:block;margin:0 auto 11px;width:240px;height:35px;border:1px solid var(--line);text-align:left;font-size:11px;padding:10px 14px;color:var(--muted)}
.optin .fields{margin-top:14px}
.btn-join{display:flex;margin:6px auto 0;width:240px;height:37px;background:var(--red);color:#fff;border-radius:3px;font-family:"Roboto",sans-serif;font-size:13px;font-weight:700;align-items:center;justify-content:center;gap:6px}

/* courses */
.courses{left:0;top:1360px;width:1200px;height:507px;background:#fff}
.courses h2{position:absolute;top:52px;width:100%;text-align:center;font-family:"Roboto",sans-serif;font-size:26px;font-weight:400;color:var(--ink)}
.courses .lede{position:absolute;top:93px;width:100%;text-align:center;font-style:italic;font-size:12px}
.course{position:absolute;top:140px;width:240px;text-align:center}
.course-photo{width:160px;height:160px;margin:0 auto;border-radius:50%;border:6px solid #fff;box-shadow:0 0 0 1px #e4e4e4,0 2px 6px rgba(0,0,0,.12)}
.course h3{margin-top:14px;font-family:"Roboto",sans-serif;font-size:13.5px;font-weight:500;color:var(--ink);line-height:23px}
.course p{margin-top:4px;font-size:11px;line-height:20px;padding:0 10px}
.btn-learn{display:inline-flex;margin-top:12px;width:114px;height:35px;background:var(--slate);color:#fff;border-radius:3px;font-family:"Roboto",sans-serif;font-size:11.5px;align-items:center;justify-content:center;gap:6px;box-shadow:0 2px 0 var(--slate-deep)}
.flow{position:absolute;top:215px}

/* testimonials */
.testimonials{left:0;top:1867px;width:1200px;height:316px;background:linear-gradient(180deg,#3d3733 0%,#2a2624 55%,#3a3532 100%)}
.testimonials h2{position:absolute;top:58px;width:100%;text-align:center;font-family:"Roboto",sans-serif;font-size:25px;font-weight:500;color:#fff}
.t-nav{position:absolute;right:108px;top:60px;color:#aaa;font-size:14px;letter-spacing:6px}
.t-photo{position:absolute;left:162px;top:111px;width:132px;height:132px;border-radius:50%;border:4px solid #fff;background:linear-gradient(160deg,#8e8a86,#4a4442)}
.t-body{position:absolute;left:329px;top:111px;width:720px;color:#fff}
.t-body h3{font-family:"Roboto",sans-serif;font-size:14px;font-weight:500}
.t-body blockquote{margin-top:14px;font-style:italic;font-size:11px;line-height:23px;padding-left:40px;position:relative}
.q{position:absolute;font-family:Georgia,serif;font-size:34px;color:#ddd;font-style:normal;line-height:1}
.t-body cite{display:block;margin-top:8px;font-style:normal;font-family:"Roboto",sans-serif;font-weight:700;font-size:11.5px;letter-spacing:.4px}

/* footer */
.footer{left:0;top:2183px;width:1200px;height:101px;background:var(--slate)}
.footer .brand{left:99px;top:32px}
.footer .brand-mark{background:#fff;opacity:.9}
.footer .brand-name{color:#fff}
.foot-links{position:absolute;left:375px;top:27px;color:#fff;font-family:"Roboto",sans-serif;font-size:12px;line-height:26px}
.foot-links .copy{font-size:11.5px}
.follow{position:absolute;left:906px;top:34px;display:flex;align-items:center;gap:6px;color:#fff;font-family:"Roboto",sans-serif;font-size:12px}
.follow b{font-weight:500;margin-right:4px}
.social{width:28px;height:28px;border-radius:50%;background:#fff}
</style>
</head>
<body>
<div class="page">

  <header class="header">
    <div class="abs brand">
      <span class="brand-mark"></span>
      <span class="brand-name">Bright Fern Studies</span>
    </div>
    <div class="abs search">Enter any keyword.
      <svg width="11" height="11" viewBox="0 0 11 11" aria-hidden="true"><circle cx="4.5" cy="4.5" r="3.4" fill="none" stroke="#555" stroke-width="1.4"/><line x1="7" y1="7" x2="10" y2="10" stroke="#555" stroke-width="1.6"/></svg>
    </div>
    <nav class="abs nav">
      <a class="active">HOME</a><a>ABOUT</a><a>COURSES</a><a>BLOG</a><a>STUDENT AREAS</a><a>CONTACT</a>
    </nav>
  </header>

  <section class="abs hero" role="img" aria-label="Photo of hands typing on a laptop keyboard beside a window with greenery"></section>
  <svg class="abs hero-arrow" style="left:50px" width="24" height="60" viewBox="0 0 24 60" aria-hidden="true"><polyline points="20,2 3,30 20,58" fill="none" stroke="#fff" stroke-width="1.5" opacity=".8"/></svg>
  <svg class="abs hero-arrow" style="left:1126px" width="24" height="60" viewBox="0 0 24 60" aria-hidden="true"><polyline points="4,2 21,30 4,58" fill="none" stroke="#fff" stroke-width="1.5" opacity=".8"/></svg>
  <div class="abs hero-kicker">ONLINE COURSES</div>
  <h1 class="abs hero-title">REIKI AND WELLNESS SELF-DEVELOPMENT</h1>

  <section class="abs features"></section>
  <article class="abs feature" style="left:99px">
    <h3>How Reiki Works</h3>
    <p style="top:138px;left:26px;right:26px">Reiki has been used for centuries to help individuals with physical and emotional imbalances as well as seeking clarity and enlightenment...</p>
  </article>
  <article class="abs feature alt" style="left:433px">
    <h3>Traditional Usui Reiki Master<br>Certification</h3>
    <p style="top:160px;left:50px;right:50px">Learn how to use Reiki to help yourself and others.</p>
  </article>
  <article class="abs feature" style="left:766px">
    <h3>Resources</h3>
    <p style="top:138px;left:45px;right:45px">Information and tools to help you create a life you love.</p>
  </article>
  <div class="abs diamond" role="img" aria-label="Photo of a man relaxing during a Reiki session" style="left:199px;top:578px;background:linear-gradient(135deg,#2a2a2a,#c9a48a 55%,#eee)"></div>
  <div class="abs diamond" role="img" aria-label="Photo of stacked stones on a beach at sunset" style="left:533px;top:578px;background:linear-gradient(135deg,#b7c6dc,#e9d2bf 50%,#8c7a6a)"></div>
  <div class="abs diamond" role="img" aria-label="Photo of smooth rocks in calm blue sea water" style="left:866px;top:578px;background:linear-gradient(135deg,#cfe0ee,#4c7ea5 50%,#d8cbb2)"></div>

  <section class="abs welcome">
    <h2>Welcome to Bright Fern Studies</h2>
    <div class="copy">
      <p>Thought to be centuries old and rediscovered in the late 1800's, Reiki (pronounced ray-key) is a healing and enlightenment system. Reiki can be translated into "Universal (Rei) Life Energy (Ki)". As a practitioner of Reiki, you attune your awareness to this energy and utilize it for the physical and emotional healing of self and others...</p>
      <p>Reiki is non-denominational and can be practiced by everyone, regardless of their religious and spiritual beliefs. Reiki can be performed hands-on in person or from a distance.</p>
      <p>Have you ever seen a mother kiss a child's elbow after they fall? What is your response when you stub your toe or bang your shin? We instinctively touch and focus on areas in pain or need. Reiki is an extension of this innate wisdom.</p>
    </div>
    <div class="btn-more"><span>Read More Info</span><i><svg width="10" height="14" viewBox="0 0 10 14" aria-hidden="true"><polyline points="2,2 7,7 2,12" fill="none" stroke="#fff" stroke-width="2.2"/></svg></i></div>
    <form class="optin">
      <h3>Stay Inspired</h3>
      <p>Receive information and articles each month to keep you feeling inspired...</p>
      <div class="fields">
        <span class="field">First Name*</span>
        <span class="field">Last Name*</span>
        <span class="field">E-mail Address*</span>
      </div>
      <span class="btn-join">YES-COUNT ME IN <svg width="8" height="11" viewBox="0 0 8 11" aria-hidden="true"><polyline points="1.5,1.5 5.5,5.5 1.5,9.5" fill="none" stroke="#fff" stroke-width="2"/></svg></span>
    </form>
  </section>

  <section class="abs courses">
    <h2>Courses</h2>
    <p class="lede">Sed ut perspiciatis unde omnis iste natus error sit voluptatem accusantium doloremque laudantium, totam...</p>

    <svg class="flow" style="left:285px" width="80" height="40" viewBox="0 0 80 40" aria-hidden="true"><path d="M2 6 Q40 4 70 30" fill="none" stroke="#ccc" stroke-width="2" stroke-dasharray="2 4"/><polyline points="62,30 71,31 70,22" fill="none" stroke="#ccc" stroke-width="2"/></svg>
    <svg class="flow" style="left:545px;top:185px" width="90" height="50" viewBox="0 0 90 50" aria-hidden="true"><path d="M2 44 Q45 46 80 10" fill="none" stroke="#ccc" stroke-width="2" stroke-dasharray="2 4"/><polyline points="72,9 81,9 80,18" fill="none" stroke="#ccc" stroke-width="2"/></svg>
    <svg class="flow" style="left:820px" width="80" height="40" viewBox="0 0 80 40" aria-hidden="true"><path d="M2 6 Q40 4 70 30" fill="none" stroke="#ccc" stroke-width="2" stroke-dasharray="2 4"/><polyline points="62,30 71,31 70,22" fill="none" stroke="#ccc" stroke-width="2"/></svg>

    <article class="course" style="left:83px">
      <div class="course-photo" role="img" aria-label="Photo of a stone stack topped with a purple flower" style="background:radial-gradient(circle at 50% 45%,#2e2e2e 0 30%,#c4623a 60%,#e79a62)"></div>
      <h3>Reiki Level I, II and Master<br>Certification</h3>
      <p>Nemo enim ipsam voluptatem quia volup aspernatur aut odit aut fugit...</p>
      <span class="btn-learn">Learn More <svg width="14" height="8" viewBox="0 0 14 8" aria-hidden="true"><path d="M0 4h11M8 1l3 3-3 3" fill="none" stroke="#fff" stroke-width="1.6"/></svg></span>
    </article>
    <article class="course" style="left:340px">
      <div class="course-photo" role="img" aria-label="Photo of a small white dog sitting with a person in meditation" style="background:linear-gradient(180deg,#6f8fc2,#c9d3e4 55%,#f2efe9)"></div>
      <h3>Animal Reiki Practitioner<br>Certification</h3>
      <p>Nemo enim ipsam voluptatem quia volup aspernatur aut odit aut fugit...</p>
      <span class="btn-learn">Learn More <svg width="14" height="8" viewBox="0 0 14 8" aria-hidden="true"><path d="M0 4h11M8 1l3 3-3 3" fill="none" stroke="#fff" stroke-width="1.6"/></svg></span>
    </article>
    <article class="course" style="left:620px">
      <div class="course-photo" role="img" aria-label="Photo of a therapist giving an acupressure treatment" style="background:linear-gradient(160deg,#4a2a16,#b8763d 50%,#e3c9a6)"></div>
      <h3>Acupressure and Reiki for Anxiety<br>and Depression</h3>
      <p>Nemo enim ipsam voluptatem quia volup aspernatur aut odit aut fugit...</p>
      <span class="btn-learn">Learn More <svg width="14" height="8" viewBox="0 0 14 8" aria-hidden="true"><path d="M0 4h11M8 1l3 3-3 3" fill="none" stroke="#fff" stroke-width="1.6"/></svg></span>
    </article>
    <article class="course" style="left:875px">
      <div class="course-photo" role="img" aria-label="Photo of a meditating silhouette against a sunset sky" style="background:linear-gradient(180deg,#f2b255,#ee8a3c 55%,#7a4a3a)"></div>
      <h3>Your Soul is Calling: Creating<br>Your Ideal Life</h3>
      <p>Nemo enim ipsam voluptatem quia volup aspernatur aut odit aut fugit...</p>
      <span class="btn-learn">Learn More <svg width="14" height="8" viewBox="0 0 14 8" aria-hidden="true"><path d="M0 4h11M8 1l3 3-3 3" fill="none" stroke="#fff" stroke-width="1.6"/></svg></span>
    </article>
  </section>

  <section class="abs testimonials" role="group" aria-label="Testimonials, set over a dim photo of stacked pebbles">
    <h2>Testimonials</h2>
    <div class="t-nav">‹ ›</div>
    <div class="t-photo" role="img" aria-label="Portrait photo of the student"></div>
    <div class="t-body">
      <h3>A very thorough and authentic training</h3>
      <blockquote>
        <span class="q" style="left:0;top:0">“</span>
        I really loved this course. The lectures were enjoyable to listen to. It was a great feature to offer them as additional downloads. The extra material like the guided meditations were all high quality. As someone very familiar with Japanese culture I really appreciated the accuracy and authenticity of the material as well as the thoroughness of the training, covering many techniques and methods...<b style="font-style:normal">Read More &gt;&gt;</b>
        <cite style="margin-left:-40px">-MARISOL WHITCOMBE</cite>
      </blockquote>
    </div>
    <span class="q" style="left:986px;top:214px">”</span>
  </section>

  <footer class="abs footer">
    <div class="abs brand">
      <span class="brand-mark"></span>
      <span class="brand-name">Bright Fern Studies</span>
    </div>
    <div class="foot-links">
      <div>Home &nbsp;| &nbsp;About &nbsp;| &nbsp;Courses &nbsp;| &nbsp;Blog &nbsp;| &nbsp;Student Areas &nbsp;| &nbsp;Contact</div>
      <div class="copy">Copyrights © 2016 . brightfernstudies.example | Allrights Reserved.</div>
    </div>
    <div class="follow">
      <b>Follow Us :</b>
      <span class="social" aria-label="Social profile 1"></span>
      <span class="social" aria-label="Social profile 2"></span>
      <span class="social" aria-label="Social profile 3"></span>
      <span class="social" aria-label="Social profile 4"></span>
    </div>
  </footer>

</div>
</body>
</html>
```